Business Card & Letterhead Design

We a financial advice company based in Australia. We provide advice to wealthy farmers.

We are changing our business name FROM Brightvale Financial TO Tallowmere Wealth and we need a new letterhead and double sided business card design

Attached is designs from our previous branding (Brightvale Financial) as it includes all the details we require on the new Tallowmere Wealth business cards and letterhead.

Need extra days to review

```html
<!DOCTYPE html>
<html lang="en">
<head>
<meta charset="utf-8">
<title>Tallowmere Wealth – Letterhead &amp; Business Card</title>
<link href="https://fonts.googleapis.com/css2?family=Open+Sans:ital,wght@0,400;0,600;0,700;1,400;1,700&display=swap" rel="stylesheet">
<style>
  :root{
    --bg:#e4e5e6;
    --paper:#ffffff;
    --charcoal:#3c3f42;
    --ink:#2b2b2b;
    --muted:#6d6f72;
    --beige:#d9d2c6;
    --strip:#8d9094;
    --light-text:#eceded;
  }
  *{margin:0;padding:0;box-sizing:border-box}
  html,body{width:1200px;height:738px;overflow:hidden;background:var(--bg);font-family:"Open Sans",sans-serif;color:var(--ink)}
  address{font-style:normal}
  .canvas{position:relative;width:1200px;height:738px}

  /* Letterhead */
  .letterhead{position:absolute;left:40px;top:19px;width:495px;height:700px;background:var(--paper);box-shadow:0 2px 8px rgba(0,0,0,.15);overflow:hidden}
  .letterhead .wave{position:absolute;left:0;top:0}
  .brand{position:absolute;display:flex;flex-direction:column;align-items:center}
  .brand-mark{border:1.5px solid var(--charcoal);border-radius:50%}
  .brand-name{font-weight:600;color:var(--charcoal);letter-spacing:.12em;text-transform:uppercase;white-space:nowrap}
  .letterhead .brand{left:0;right:0;top:18px}
  .letterhead .brand-mark{width:28px;height:28px;margin-bottom:4px}
  .letterhead .brand-name{font-size:13px}
  .watermark{position:absolute;left:170px;top:270px;width:170px;height:170px;border:14px solid rgba(60,63,66,.07);border-radius:50%}
  .salutation{position:absolute;left:36px;top:84px;font-size:7.6px;color:var(--ink)}
  .recipient{position:absolute;right:24px;top:72px;font-size:7px;line-height:1.35;color:var(--muted);text-align:right}
  .letter-body{position:absolute;left:36px;right:36px;top:150px;font-size:7.6px;line-height:1.45;color:var(--ink);text-align:justify}
  .letter-body p{margin-bottom:7px;text-indent:28px}
  .licensee{position:absolute;left:20px;top:584px;font-size:6.6px;line-height:1.4;color:var(--light-text)}
  .lh-address{position:absolute;left:200px;top:612px;font-size:6.6px;line-height:1.4;color:var(--light-text)}
  .lh-contact{position:absolute;left:362px;top:624px;font-size:7px;line-height:1.9;color:var(--light-text)}
  .contact-row{display:flex;align-items:center;gap:5px}
  .contact-row svg{flex:none}
  .lh-strip{position:absolute;left:0;right:0;bottom:0;height:18px;background:var(--strip);color:#fff;font-weight:700;font-style:italic;font-size:8px;line-height:18px;padding-left:20px;letter-spacing:.03em}

  /* Business card */
  .card{position:absolute;left:580px;top:203px;width:580px;height:332px;background:var(--paper);box-shadow:0 2px 8px rgba(0,0,0,.18);overflow:hidden}
  .card .wave{position:absolute;left:0;top:0}
  .card .brand{left:40px;top:20px;width:190px}
  .card .brand-mark{width:40px;height:40px;margin-bottom:6px}
  .card .brand-name{font-size:15px}
  .card-person{position:absolute;left:360px;top:118px}
  .card-person .name{font-size:19px;font-weight:600;color:var(--ink)}
  .card-person .post{font-size:9px;font-weight:400;color:var(--muted);margin-left:4px}
  .card-person .role{font-size:10px;line-height:1.4;color:var(--muted);margin-top:3px}
  .tagline{position:absolute;left:30px;top:150px;font-size:11px;font-style:italic;color:var(--charcoal)}
  .card-contacts{position:absolute;left:30px;top:210px;font-size:9.5px;line-height:1.75;color:var(--light-text)}
  .card-address{position:absolute;left:330px;top:238px;font-size:9.5px;line-height:1.4;color:var(--light-text)}
  .card-motto{position:absolute;left:330px;top:300px;font-size:10px;font-style:italic;font-weight:700;color:var(--light-text);letter-spacing:.04em}
</style>
</head>
<body>
<main class="canvas">

  <section class="letterhead" aria-label="Letterhead">
    <svg class="wave" width="495" height="700" viewBox="0 0 495 700" aria-hidden="true">
      <path d="M0,548 C150,500 300,650 495,580" fill="none" stroke="var(--beige)" stroke-width="5"/>
      <path d="M0,560 C150,512 300,662 495,592 L495,700 L0,700 Z" fill="var(--charcoal)"/>
    </svg>
    <div class="watermark" aria-hidden="true"></div>

    <header class="brand">
      <span class="brand-mark" aria-hidden="true"></span>
      <span class="brand-name">Tallowmere Wealth</span>
    </header>

    <p class="salutation">Dear Sir</p>

    <address class="recipient">
      Wendell Holdings Pty Ltd<br>
      ATF The Harrow Investment<br>
      Trust T/AS Brightvale Financial<br>
      ABN: 98 765 432 109<br>
      Corporate Authorised<br>
      Representative of Keystone<br>
      Advisory Group Limited
    </address>

    <article class="letter-body">
      <p>Lorem ipsum dolor sit amet, consectetur adipiscing elit. Integer eu odio mattis, pulvinar turpis quis, faucibus nisl. Proin feugiat, erat vitae cursus pharetra, enim est semper ligula, in malesuada orci nisl et diam. Etiam elementum metus ac fringilla vulputate. Etiam mattis ligula sed ante mollis bibendum. Orci varius natoque penatibus et magnis dis parturient montes, nascetur ridiculus mus.</p>
      <p>Ut nibh augue, blandit ac orci ac, rutrum congue enim. Suspendisse gravida vulputate felis, quis interdum orci tincidunt quis. Praesent imperdiet maximus neque. Mauris ut dui enim. Nullam at efficitur elit. Donec ante ipsum, fermentum at lectus vel, blandit vulputate ante. Proin luctus suscipit diam id vestibulum. Morbi malesuada id mauris eget ullamcorper.</p>
      <p>Donec varius orci purus, vitae aliquam libero volutpat id. Integer sed imperdiet libero. Aliquam accumsan, risus sit amet ornare consectetur, turpis felis dictum justo, non rhoncus mauris dui sed velit. Pellentesque habitant morbi tristique senectus et netus et malesuada fames ac turpis egestas. Pellentesque tincidunt vitae ligula nec imperdiet. Donec sed congue enim. Nullam elementum faucibus nulla nec vestibulum. Sed at tempor ligula. In quis vulputate nunc. Integer at gravida lacus, ac tristique risus. Sed at vulputate nulla.</p>
      <p>Praesent blandit nunc eu efficitur commodo. In tempor nisl ex, vel venenatis ante vestibulum a. Duis vestibulum nibh a erat sagittis, nec euismod lorem varius. Nam ultricies turpis sed justo sollicitudin volutpat. Morbi sed mollis eros. Sed quis tortor id enim vehicula porttitor. Curabitur non aliquam ex. Phasellus dignissim fermentum elit, at finibus ligula mattis eget.</p>
    </article>

    <address class="licensee">
      Keystone Advisory Group Limited<br>
      ABN 12 345 678 901<br>
      Australian Financial Services Licence<br>
      Licence Number 456 789<br>
      Principle Address: 120 Harbour Rd<br>
      PO Box 4410 Southbank VIC 3006
    </address>

    <address class="lh-address">
      Suite 4A, 18 Marlow St<br>
      Riverbend QLD 4100<br>
      PO Box 1180<br>
      Riverbend QLD 4100
    </address>

    <div class="lh-contact">
      <div class="contact-row">
        <svg width="9" height="9" viewBox="0 0 10 10" aria-hidden="true"><path d="M2,1 L4,1 L4.6,3 L3.4,4 C4,5.4 4.8,6.2 6,6.8 L7,5.6 L9,6.2 L9,8.2 C5,8.6 1.4,5 2,1 Z" fill="var(--light-text)"/></svg>
        (07) 3000 1100
      </div>
      <div class="contact-row">
        <svg width="9" height="9" viewBox="0 0 10 10" aria-hidden="true"><rect x="1" y="4" width="8" height="5" fill="var(--light-text)"/><rect x="2.5" y="1" width="5" height="3" fill="none" stroke="var(--light-text)"/></svg>
        (07) 3000 1122
      </div>
      <div>www.brightvalefinancial.com.au</div>
    </div>

    <div class="lh-strip">A referral built business</div>
  </section>

  <section class="card" aria-label="Business card">
    <svg class="wave" width="580" height="332" viewBox="0 0 580 332" aria-hidden="true">
      <path d="M0,180 C160,130 330,240 580,160" fill="none" stroke="var(--beige)" stroke-width="6"/>
      <path d="M0,192 C160,142 330,252 580,172 L580,332 L0,332 Z" fill="var(--charcoal)"/>
    </svg>

    <header class="brand">
      <span class="brand-mark" aria-hidden="true"></span>
      <span class="brand-name">Tallowmere Wealth</span>
    </header>

    <div class="card-person">
      <div class="name">Tom Ridley<span class="post">B.Com Dip.FP</span></div>
      <div class="role">Managing Director<br>Authorised Representative</div>
    </div>

    <p class="tagline">‘Financial peace of mind’</p>

    <div class="card-contacts">
      <div class="contact-row">
        <svg width="10" height="10" viewBox="0 0 10 10" aria-hidden="true"><path d="M2,1 L4,1 L4.6,3 L3.4,4 C4,5.4 4.8,6.2 6,6.8 L7,5.6 L9,6.2 L9,8.2 C5,8.6 1.4,5 2,1 Z" fill="var(--light-text)"/></svg>
        (07) 3000 1100
      </div>
      <div class="contact-row">
        <svg width="10" height="10" viewBox="0 0 10 10" aria-hidden="true"><rect x="1" y="4" width="8" height="5" fill="var(--light-text)"/><rect x="2.5" y="1" width="5" height="3" fill="none" stroke="var(--light-text)"/></svg>
        (07) 3000 1122
      </div>
      <div class="contact-row">
        <svg width="10" height="10" viewBox="0 0 10 10" aria-hidden="true"><rect x="2.5" y="0.5" width="5" height="9" rx="1" fill="none" stroke="var(--light-text)"/></svg>
        0400 000 111
      </div>
      <div class="contact-row">
        <svg width="10" height="10" viewBox="0 0 10 10" aria-hidden="true"><rect x="0.5" y="2" width="9" height="6" fill="none" stroke="var(--light-text)"/><path d="M0.5,2 L5,5.5 L9.5,2" fill="none" stroke="var(--light-text)"/></svg>
        tom@brightvalefinancial.com.au
      </div>
      <div class="contact-row">
        <svg width="10" height="10" viewBox="0 0 10 10" aria-hidden="true"><circle cx="5" cy="5" r="4.2" fill="none" stroke="var(--light-text)"/><path d="M1,5 H9 M5,1 C3,3.5 3,6.5 5,9 M5,1 C7,3.5 7,6.5 5,9" fill="none" stroke="var(--light-text)" stroke-width=".7"/></svg>
        www.brightvalefinancial.com.au
      </div>
    </div>

    <address class="card-address">
      Suite 4A, 18 Marlow St<br>
      Riverbend QLD 4100<br>
      PO Box 1180<br>
      Riverbend QLD 4100
    </address>

    <p class="card-motto">A referral built business</p>
  </section>

</main>
</body>
</html>
```